Harborline Auto LLC

Car Dealer Customer Service
Address: 2874 Cresthaven Road, Shelbyville, TN 37162
web: www.harborlineautoxq.net
email: harborlineautoxq@mailnest.example
Phone: (931) 555-0148
Phone: (629) 555-0173

```html
<!DOCTYPE html>
<html lang="en">
<head>
<meta charset="utf-8">
<title>Harborline Auto – Business Card</title>
<link rel="stylesheet" href="https://fonts.googleapis.com/css2?family=Montserrat:wght@700;800&family=Arimo:wght@400&family=Oswald:wght@500&display=swap">
<style>
  :root {
    --backdrop: #2a2a2c;
    --card-white: #ffffff;
    --brand-blue: #1b7fc0;
    --brand-blue-dark: #16659c;
    --brand-blue-light: #2ea3e0;
    --brand-gold: #eeb13c;
    --ink: #1f1f1f;
    --rule: #9a9a9a;
  }
  * { box-sizing: border-box; margin: 0; padding: 0; }
  html, body { width: 1200px; height: 1108px; overflow: hidden; }
  body {
    background: var(--backdrop);
    display: flex;
    align-items: center;
    justify-content: center;
    gap: 80px;
  }
  .card {
    width: 380px;
    height: 650px;
    border-radius: 22px;
    overflow: hidden;
    position: relative;
    box-shadow: 0 16px 34px rgba(0,0,0,0.45);
  }
  /* Front */
  .card--front {
    background: var(--card-white);
    display: flex;
    flex-direction: column;
    align-items: center;
    padding-top: 92px;
    text-align: center;
  }
  .brand-mark {
    width: 70px; height: 70px;
    border-radius: 50%;
    background: var(--brand-gold);
    margin-bottom: 22px;
  }
  .brand-name {
    font-family: "Montserrat", sans-serif;
    font-weight: 800;
    font-size: 33px;
    letter-spacing: 1px;
    color: var(--brand-blue);
    line-height: 1.1;
  }
  .person { margin-top: 58px; }
  .person__name {
    font-family: "Montserrat", sans-serif;
    font-weight: 700;
    font-size: 24px;
    letter-spacing: 1px;
    color: var(--brand-blue);
  }
  .person__role {
    font-family: "Arimo", sans-serif;
    font-size: 19px;
    color: var(--brand-gold);
    margin-top: 2px;
  }
  .icon-row {
    display: flex;
    align-items: center;
    gap: 8px;
    margin-top: 16px;
  }
  .icon-row__rule { width: 44px; height: 1px; background: var(--rule); }
  .icon-box {
    width: 40px; height: 40px;
    border-radius: 6px;
    background: var(--brand-blue);
    display: flex; align-items: center; justify-content: center;
  }
  .icon-box svg { width: 24px; height: 24px; }
  .contact {
    font-family: "Arimo", sans-serif;
    font-size: 19px;
    color: var(--ink);
    line-height: 1.32;
    margin-top: 16px;
  }
  .contact .accent { color: var(--brand-blue-light); }
  .contact__rule {
    width: 260px; height: 1px;
    background: var(--rule);
    margin: 14px auto;
  }
  .address {
    font-family: "Arimo", sans-serif;
    font-size: 20px;
    color: var(--ink);
    line-height: 1.35;
  }
  /* Back */
  .card--back {
    background: linear-gradient(160deg, var(--brand-blue-light) 0%, var(--brand-blue) 55%, var(--brand-blue-dark) 100%);
  }
  .back-pattern {
    position: absolute; inset: 0;
    background: linear-gradient(160deg, rgba(255,255,255,0.08), rgba(0,0,0,0.08));
  }
  .back-badge {
    position: absolute;
    left: 242px; top: 400px;
    width: 62px; height: 62px;
    border-radius: 50%;
    background: var(--card-white);
  }
  .tagline {
    position: absolute;
    left: 0; right: 0; bottom: 60px;
    text-align: center;
    font-family: "Oswald", sans-serif;
    font-weight: 500;
    font-size: 31px;
    letter-spacing: 1px;
    color: var(--brand-gold);
    text-transform: uppercase;
  }
</style>
</head>
<body>
  <section class="card card--front" aria-label="Business card front">
    <div class="brand-mark"></div>
    <h1 class="brand-name">HARBORLINE AUTO</h1>

    <div class="person">
      <p class="person__name">MARCUS ELLERY</p>
      <p class="person__role">Managing Director</p>
    </div>

    <div class="icon-row">
      <span class="icon-row__rule"></span>
      <span class="icon-box" aria-label="Phone">
        <svg viewBox="0 0 24 24"><path fill="#fff" d="M6.6 10.8a15.1 15.1 0 0 0 6.6 6.6l2.2-2.2c.3-.3.7-.4 1-.2 1.1.4 2.3.6 3.6.6.6 0 1 .4 1 1V20c0 .6-.4 1-1 1A17 17 0 0 1 3 4c0-.6.4-1 1-1h3.5c.6 0 1 .4 1 1 0 1.3.2 2.5.6 3.6.1.3 0 .7-.2 1z"/></svg>
      </span>
      <span class="icon-box" aria-label="Phone">
        <svg viewBox="0 0 24 24"><path fill="#fff" d="M6.6 10.8a15.1 15.1 0 0 0 6.6 6.6l2.2-2.2c.3-.3.7-.4 1-.2 1.1.4 2.3.6 3.6.6.6 0 1 .4 1 1V20c0 .6-.4 1-1 1A17 17 0 0 1 3 4c0-.6.4-1 1-1h3.5c.6 0 1 .4 1 1 0 1.3.2 2.5.6 3.6.1.3 0 .7-.2 1z"/></svg>
      </span>
      <span class="icon-box" aria-label="Website">
        <svg viewBox="0 0 24 24" fill="none" stroke="#fff" stroke-width="1.8"><circle cx="12" cy="12" r="9"/><ellipse cx="12" cy="12" rx="4" ry="9"/><path d="M3 12h18"/></svg>
      </span>
      <span class="icon-box" aria-label="Email">
        <svg viewBox="0 0 24 24" fill="none" stroke="#fff" stroke-width="1.8"><rect x="3" y="6" width="18" height="12"/><path d="M3 6l9 7 9-7"/></svg>
      </span>
      <span class="icon-row__rule"></span>
    </div>

    <div class="contact">
      <p>(931) 555-0148</p>
      <p>(629) 555-0173</p>
      <p>www.<span class="accent">harborlineautoxq</span>.net</p>
      <p>harborlineautoxq@mailnest.example</p>
    </div>
    <div class="contact__rule"></div>
    <address class="address">
      2874 Cresthaven Road<br>Shelbyville, TN 37162
    </address>
  </section>

  <section class="card card--back" aria-label="Business card back">
    <div class="back-pattern" role="img" aria-label="Embossed repeating brand pattern on blue"></div>
    <div class="back-badge"></div>
    <p class="tagline">Car Dealer Customer Service</p>
  </section>
</body>
</html>
```